Supplement Bottle Label Design and Creative Lifestyle Images

We are a medical home consumer brand and we are releasing a supplement line of products called "Veltrix Wellness". We are in need of a supplement bottle design for our supplement line, Veltrix Wellness. We are looking for a very appealing, simple, and clean design, but with a medical feel to it.

We would like to see designs with a black background as well as designs with a white background. Bottle size will approximately be 200cc and label will about be 7" x 2.5", but this size is subject to change.

We really like the Brenna Nutrition design and the Field Kinetics, however, we like the medical style of Nutrition Cornerstone. Please reference the links below.

To start off, the title of this bottle will be "Mindalux". We will need all similar warning about HRB, made in USA, non-GMA, GMP, ect. Please use the formula below to start:

2 Pills per serving
Blueberry pterostilbene - 10mg
Bacopa - 150mg
Gingko Biloba - 50mg
Vinpocetine - 10mg
Alpha-GPC -150mg
TAU - 35mg

https://www.shopvarlo.example/Brenna-Nutrition/b/ref=bl_dp_s_web_48213906722?ie=UTF8&node=48213906722&field-lbr_brands_browse-bin=Brenna+Nutrition

https://www.shopvarlo.example/l/7394025188

https://www.shopvarlo.example/Nutrition-Cornerstone/b/ref=bl_dp_s_web_56071238493?ie=UTF8&node=56071238493&field-lbr_brands_browse-bin=Nutrition+Cornerstone

```html
<!DOCTYPE html>
<html lang="en">
<head>
<meta charset="utf-8">
<title>Mindalux Label</title>
<link href="https://fonts.googleapis.com/css2?family=Exo+2:ital,wght@0,300;0,400;0,600;0,700;1,400&family=Oswald:wght@400;500&family=Roboto+Condensed:wght@300;400;700&display=swap" rel="stylesheet">
<style>
  :root {
    --ink: #050607;
    --panel: #0d0f12;
    --blue: #1e9fe0;
    --blue-deep: #0b5f9c;
    --blue-light: #5cc6f5;
    --white: #ffffff;
    --soft: #c9d3da;
    --page: #f1f2f3;
    --accent-red: #d3202f;
  }
  * { box-sizing: border-box; margin: 0; padding: 0; }
  html, body { width: 1200px; height: 857px; overflow: hidden; background: var(--page); }
  body { position: relative; font-family: "Roboto Condensed", sans-serif; color: var(--white); }

  .label {
    position: absolute; left: 20px; top: 128px; width: 1160px; height: 600px;
    background: linear-gradient(180deg, #15181c 0%, var(--ink) 55%, var(--panel) 100%);
    border-radius: 6px; overflow: hidden;
  }
  .top-stripe { position: absolute; left: 0; top: 58px; width: 100%; height: 12px; background: var(--blue); }
  .bottom-band {
    position: absolute; left: 0; top: 420px; width: 100%; height: 140px;
    background: linear-gradient(135deg, var(--blue-deep) 0%, var(--blue) 50%, var(--blue-deep) 100%);
  }
  .panel-divider { position: absolute; top: 70px; width: 1px; height: 490px; background: rgba(255,255,255,0.06); }

  /* Center panel */
  .brand-tab {
    position: absolute; left: 395px; top: 58px; width: 370px; height: 72px;
    background: linear-gradient(180deg, var(--blue-light), var(--blue));
    border-radius: 0 0 28px 28px;
    display: flex; align-items: center; justify-content: center;
  }
  .brand-name { font-family: "Exo 2", sans-serif; font-weight: 700; font-size: 44px; color: var(--white); letter-spacing: 1px; }
  .product-title {
    position: absolute; left: 380px; top: 176px; width: 400px; text-align: center; white-space: nowrap;
    font-family: "Exo 2", sans-serif; font-weight: 300; font-size: 68px; letter-spacing: 3px; line-height: 1;
  }
  .product-title .dot { display: inline-block; width: 12px; height: 12px; border-radius: 50%; background: var(--accent-red); vertical-align: middle; margin-left: 4px; }
  .tagline {
    position: absolute; left: 380px; top: 282px; width: 400px; text-align: center;
    font-family: "Exo 2", sans-serif; font-style: italic; font-size: 21px; color: var(--white);
  }
  .benefits { position: absolute; left: 392px; top: 336px; width: 376px; display: flex; justify-content: space-between; }
  .benefit {
    display: flex; align-items: center; gap: 8px; height: 38px; padding: 0 12px;
    background: linear-gradient(180deg, var(--blue-light), var(--blue)); border-radius: 19px;
    font-family: "Oswald", sans-serif; font-size: 13px; letter-spacing: 0.2px; text-transform: uppercase;
  }
  .benefit .num {
    width: 30px; height: 30px; border-radius: 50%; background: #1b2a52; border: 2px solid var(--white);
    display: flex; align-items: center; justify-content: center; font-size: 16px;
  }
  .category { position: absolute; left: 410px; top: 436px; font-family: "Oswald", sans-serif; font-size: 22px; letter-spacing: 2px; line-height: 1.45; }
  .count { position: absolute; left: 600px; top: 492px; display: flex; align-items: center; gap: 8px; }
  .count .qty { font-family: "Oswald", sans-serif; font-weight: 500; font-size: 54px; line-height: 1; }
  .count .unit { font-family: "Roboto Condensed", sans-serif; font-weight: 300; font-size: 20px; line-height: 1.05; color: var(--soft); }

  /* Left panel */
  .directions { position: absolute; left: 36px; top: 96px; width: 320px; font-size: 12.5px; line-height: 1.35; color: var(--soft); text-align: justify; }
  .directions p { margin-bottom: 10px; }
  .directions strong { color: var(--white); font-weight: 700; font-style: italic; }
  .disclaimer { border: 1px solid var(--white); padding: 6px 8px; color: var(--white); }
  .distributor { position: absolute; left: 36px; top: 440px; font-family: "Roboto Condensed", sans-serif; font-weight: 700; font-size: 15px; line-height: 1.9; }

  /* Right panel */
  .facts { position: absolute; left: 800px; top: 92px; width: 326px; background: var(--ink); border: 2px solid var(--white); }
  .facts-title { background: var(--blue); padding: 4px 10px; font-family: "Exo 2", sans-serif; font-size: 28px; line-height: 1.1; }
  .facts-meta { padding: 5px 12px 6px; font-weight: 700; font-size: 14px; line-height: 1.25; border-bottom: 6px solid var(--white); }
  .facts-head { display: flex; justify-content: space-between; padding: 3px 10px; font-size: 11px; border-bottom: 1px solid var(--white); }
  .facts-row { display: flex; justify-content: space-between; padding: 3px 10px; font-size: 13.5px; line-height: 1.3; border-bottom: 1px solid var(--white); }
  .facts-row:last-of-type { border-bottom: 4px solid var(--white); }
  .facts-row .name { font-weight: 700; }
  .facts-row small { font-weight: 400; font-size: 11px; }
  .facts-note { padding: 4px 10px; font-size: 13px; }
  .warning { position: absolute; left: 800px; top: 434px; width: 330px; font-size: 12px; line-height: 1.3; text-transform: uppercase; }
  .badges { position: absolute; left: 806px; top: 494px; display: flex; gap: 16px; }
  .badge { width: 46px; height: 46px; border-radius: 50%; background: var(--white); border: 3px solid #1b2a52; }
  .badge.shield { border-radius: 6px 6px 22px 22px; }
</style>
</head>
<body>
  <div class="label">
    <div class="top-stripe"></div>
    <div class="bottom-band"></div>
    <div class="panel-divider" style="left:380px"></div>
    <div class="panel-divider" style="left:780px"></div>

    <section class="panel-left">
      <div class="directions">
        <p><strong>SUGGESTED USE:</strong> As a dietary supplement, take two (2) capsules daily. Do not exceed two (2) capsules per day, or use as directed by your health care professional.</p>
        <p><strong>CAUTION:</strong> Do not exceed recommended dose. Ginkgo Biloba and Vinpocetine may increase the risk of bleeding. Avoid in patients at risk of bleeding, taking anticoagulants, or with clotting disorders. Discontinue 2-3 weeks prior to surgical and dental procedures. Use cautiously with history of seizure. Consult your doctor if pregnant, nursing or taking any medication.</p>
        <p class="disclaimer">These statements have not been evaluated by the Health Regulatory Board. This product is not intended to diagnose, treat, cure or prevent any disease.</p>
      </div>
      <div class="distributor">Distributed by:<br>Veltrix Wellness<br>Mail Address and Phone</div>
    </section>

    <section class="panel-center">
      <div class="brand-tab"><span class="brand-name">Veltrix</span></div>
      <h1 class="product-title">MINDALUX<span class="dot"></span></h1>
      <p class="tagline">Advanced Brain and Memory Formula</p>
      <div class="benefits">
        <div class="benefit">Memory Function Aid <span class="num">1.</span></div>
        <div class="benefit"><span class="num">2.</span> Support Mental Focus</div>
      </div>
      <div class="category">DIATARY<br>SUPPLEMENT</div>
      <div class="count"><span class="qty">30</span><span class="unit">VEG<br>CAPSULES</span></div>
    </section>

    <section class="panel-right">
      <div class="facts">
        <div class="facts-title">Supplement Facts</div>
        <div class="facts-meta">Serving Size: 2 Capsules<br>Servings Per Container: 15</div>
        <div class="facts-head"><span>Amount Per Serving</span><span>% DV</span></div>
        <div class="facts-row"><span class="name">Blueberry Pterostilbene</span><span>10 mg &nbsp;†</span></div>
        <div class="facts-row"><span class="name">Bacopa <small>(Bacopa monnieri)</small></span><span>150 mg &nbsp;†</span></div>
        <div class="facts-row"><span class="name">Ginkgo Biloba <small>(leaf extract)</small></span><span>50 mg &nbsp;†</span></div>
        <div class="facts-row"><span class="name">Vinpocetine</span><span>10 mg &nbsp;†</span></div>
        <div class="facts-row"><span class="name">Alpha-GPC</span><span>150 mg &nbsp;†</span></div>
        <div class="facts-row"><span class="name">TAU</span><span>35 mg &nbsp;†</span></div>
        <div class="facts-note">† % Daily Value (DV) not established</div>
      </div>
      <p class="warning">Keep out of the reach of children. Do not use if safety seal is damaged or missing. Store at room temperature.</p>
      <div class="badges">
        <div class="badge"></div>
        <div class="badge shield"></div>
        <div class="badge"></div>
        <div class="badge"></div>
        <div class="badge"></div>
      </div>
    </section>
  </div>
</body>
</html>
```